Brake Test Training for Coal Mining

We offer Brake Test Training for Coal Mine workers. It's a legislative requirement that workers who are tasked with performing brake testing have certain competencies to do so. We test Light Vehicles and trailers, Heavy Vehicles and Mobile Mining Equipment like Graders, Scrapers and Dump Trucks.

```html
<!DOCTYPE html>
<html lang="en">
<head>
<meta charset="utf-8">
<title>Brake Test Training – Coal Mine Workers</title>
<link rel="stylesheet" href="https://fonts.googleapis.com/css2?family=Bebas+Neue&family=Montserrat:wght@600;700;800&display=swap">
<style>
  :root {
    --page: #e9e9ec;
    --navy: #23336b;
    --yellow: #f3c31c;
    --ink: #111111;
    --white: #ffffff;
    --sky: #a9c3de;
    --cloud: #eef0f2;
    --steel: #c9c6c1;
    --rock: #8a7760;
    --rock-dark: #5f5244;
    --dust: #b8a489;
  }
  * { margin: 0; padding: 0; box-sizing: border-box; }
  html, body {
    width: 1040px; height: 1200px; overflow: hidden;
    background: var(--page);
  }
  .banner {
    position: absolute; left: 0; top: 339px;
    width: 1040px; height: 522px; overflow: hidden;
    font-family: "Montserrat", Arial, sans-serif;
  }
  .site-photo {
    position: absolute; inset: 0;
    background:
      radial-gradient(ellipse 300px 150px at 330px 150px, rgba(222,220,215,.95) 0%, rgba(222,220,215,0) 100%),
      radial-gradient(ellipse 220px 120px at 150px 210px, rgba(200,196,188,.9) 0%, rgba(200,196,188,0) 100%),
      radial-gradient(ellipse 180px 110px at 600px 120px, rgba(185,182,178,.85) 0%, rgba(185,182,178,0) 100%),
      radial-gradient(ellipse 520px 260px at 900px 260px, var(--rock-dark) 0%, rgba(95,82,68,0) 100%),
      radial-gradient(ellipse 260px 90px at 380px 40px, rgba(238,240,242,.9) 0%, rgba(238,240,242,0) 100%),
      linear-gradient(180deg, var(--sky) 0%, #c6d4e2 22%, var(--dust) 46%, var(--rock) 62%, #7a6a55 100%);
  }
  .yellow-wash {
    position: absolute; inset: 0;
    background: linear-gradient(180deg, rgba(243,195,28,0) 50%, rgba(243,195,28,.6) 64%, var(--yellow) 76%, var(--yellow) 100%);
  }
  .brand {
    position: absolute; left: 782px; top: 30px;
    display: flex; align-items: center; gap: 12px;
  }
  .brand-dot {
    width: 40px; height: 40px; border-radius: 50%;
    background: var(--navy);
  }
  .brand-name {
    font-weight: 800; font-size: 16px; line-height: 1.25;
    color: var(--navy); letter-spacing: .4px;
  }
  .headline {
    position: absolute; left: 0; right: 0; top: 250px;
    text-align: center;
    font-family: "Bebas Neue", Impact, sans-serif;
    font-size: 100px; line-height: 1; letter-spacing: 3px;
    color: var(--white);
    transform: scaleY(1.3); transform-origin: top center;
    text-shadow: 3px 3px 4px rgba(0,0,0,.35);
    word-spacing: 14px;
  }
  .audience {
    position: absolute; left: 0; right: 0; top: 364px;
    text-align: center;
    font-weight: 800; font-size: 41px; line-height: 1;
    color: var(--ink); letter-spacing: -.5px;
  }
  .services {
    position: absolute; left: 0; right: 0; top: 409px;
    text-align: center;
    font-weight: 700; font-size: 17.5px; line-height: 20px;
    color: var(--ink);
  }
  .footer-wave {
    position: absolute; left: 0; bottom: 0; width: 1040px; height: 100px;
  }
  .phone {
    position: absolute; left: 660px; top: 464px;
    display: flex; align-items: center; gap: 14px;
  }
  .phone-icon { width: 36px; height: 36px; flex: none; }
  .phone-number {
    font-weight: 700; font-size: 42px; line-height: 1;
    color: var(--white); letter-spacing: .5px;
  }
</style>
</head>
<body>
  <main class="banner">
    <div class="site-photo" role="img" aria-label="Photo of a large mining excavator loading a yellow haul truck in an open-cut coal mine under a cloudy sky"></div>
    <div class="yellow-wash"></div>

    <div class="brand">
      <span class="brand-dot"></span>
      <span class="brand-name">SUMMIT<br>OPERATOR TRAINING</span>
    </div>

    <h1 class="headline">BRAKE TEST TRAINING</h1>
    <h2 class="audience">COAL MINE WORKERS</h2>
    <p class="services">We test Light Vehicles and trailers, Heavy Vehicles and Mobile Mining Equipment<br>like Graders, Scrapers and Dump Trucks.</p>

    <svg class="footer-wave" viewBox="0 0 1040 100" preserveAspectRatio="none" aria-hidden="true">
      <path d="M0 30 C 150 50, 350 95, 520 96 C 600 96, 620 46, 690 34 C 820 18, 950 16, 1040 12 L1040 100 L0 100 Z" fill="var(--navy)"/>
    </svg>

    <div class="phone">
      <svg class="phone-icon" viewBox="0 0 36 36" aria-hidden="true">
        <circle cx="18" cy="18" r="18" fill="var(--yellow)"/>
        <path d="M12.5 9.5c.8-.5 1.8-.3 2.3.5l1.6 2.6c.4.7.3 1.6-.3 2.1l-1.2 1c.8 1.8 2.2 3.3 4 4.2l1-1.2c.6-.6 1.5-.7 2.2-.3l2.6 1.6c.8.5 1 1.5.5 2.3l-.9 1.4c-.7 1.1-2.1 1.6-3.4 1.2-5-1.5-8.9-5.4-10.4-10.4-.4-1.3.1-2.7 1.2-3.4z" fill="var(--navy)"/>
      </svg>
      <span class="phone-number">1300 555 218</span>
    </div>
  </main>
</body>
</html>
```